Full service facility management

Stationery Branding needed for Envelopes, folders, letterheads to show the services we offer (valet, security, front desk/concierge, janitorial, maintenance services to CONDOMINIUMS). We need the our logo and colors to be branded to these items

Target Market(s)

Homeowner Condominiums / High Rise residential living

Font styles to use
Sans Serif

Colors
0355a3

```html
<!DOCTYPE html>
<html lang="en">
<head>
<meta charset="utf-8">
<title>Meridian Residential Services — Stationery</title>
<link rel="stylesheet" href="https://fonts.googleapis.com/css2?family=Open+Sans:wght@400&family=Roboto+Condensed:wght@400;700&display=swap">
<style>
  :root {
    --backdrop: #bdbdbd;
    --paper: #ffffff;
    --ink: #1b1919;
    --ink-soft: #333333;
    --folder: #1f1d1d;
    --band-light: #e6e6e6;
    --ghost: #f1f1f1;
    --shadow: rgba(0,0,0,0.22);
  }
  * { margin: 0; padding: 0; box-sizing: border-box; }
  html, body { width: 1200px; height: 604px; overflow: hidden; background: var(--backdrop); }
  .canvas { position: relative; width: 1200px; height: 604px; }

  .sheet { position: absolute; background: var(--paper); box-shadow: 0 1px 3px var(--shadow); overflow: hidden; }
  .letterhead { left: 68px; top: 75px; width: 340px; height: 462px; }
  .folder { left: 431px; top: 75px; width: 340px; height: 462px; background: var(--folder); }
  .envelope { left: 794px; top: 207px; width: 334px; height: 157px; }
  .card { left: 794px; top: 379px; width: 335px; height: 158px; }

  .brand { position: absolute; display: flex; align-items: flex-start; font-family: "Open Sans", sans-serif; font-weight: 400; color: var(--ink); }
  .brand-mark { flex: none; border: 1.5px solid currentColor; }
  .brand-name { line-height: 1.15; }
  .brand-name span { display: block; }
  .brand-name span:nth-child(2) { padding-left: 0.8em; }
  .brand-name span:nth-child(3) { padding-left: 4.2em; font-size: 0.55em; }

  .letterhead .brand { left: 116px; top: 37px; }
  .letterhead .brand-mark { width: 21px; height: 21px; margin-right: 6px; }
  .letterhead .brand-name { font-size: 10px; }

  .ghost-square { position: absolute; border: 10px solid var(--ghost); }
  .letterhead .ghost-square { left: 63px; top: 118px; width: 209px; height: 209px; }
  .card .ghost-square { left: 188px; top: 15px; width: 132px; height: 132px; border-width: 7px; }

  .letter-body { position: absolute; left: 34px; top: 166px; width: 272px; font-family: "Open Sans", sans-serif; font-size: 5px; line-height: 9.9px; color: var(--ink-soft); text-align: justify; }

  .signature { position: absolute; left: 242px; top: 297px; width: 66px; height: 20px; background: linear-gradient(90deg, transparent, rgba(27,25,25,0.18), transparent); }
  .signer { position: absolute; left: 260px; top: 318px; font-family: "Open Sans", sans-serif; font-size: 4px; color: var(--ink); }

  .contact-band { position: absolute; background: var(--ink); color: var(--paper); font-family: "Roboto Condensed", sans-serif; font-size: 6px; display: flex; flex-direction: column; align-items: center; justify-content: center; gap: 1px; }
  .contact-band .line-address { padding: 0 14px 2px; border-bottom: 0.6px solid currentColor; }
  .contact-band .line-reach { padding-top: 2px; }
  .contact-band b { font-weight: 700; }
  .contact-band svg { width: 5px; height: 5px; vertical-align: -0.5px; fill: currentColor; margin: 0 1px 0 2px; }
  .letterhead .contact-band, .folder .contact-band { left: 34px; top: 413px; width: 272px; height: 29px; }
  .folder .contact-band { background: var(--band-light); color: var(--ink); }
  .card .contact-band { left: 20px; top: 109px; width: 294px; height: 29px; }

  .folder .brand { left: 53px; top: 192px; color: var(--paper); }
  .folder .brand-mark { width: 70px; height: 70px; border-width: 3px; margin-right: 15px; }
  .folder .brand-name { font-size: 20px; padding-top: 8px; }

  .envelope-flap { position: absolute; left: 0; top: 0; width: 334px; height: 97px; background: var(--folder); border-radius: 0 0 14px 14px; clip-path: polygon(0 0, 100% 0, 96% 100%, 4% 100%); }
  .envelope-flap .flap-mark { position: absolute; left: 153px; top: 26px; width: 28px; height: 28px; border: 1.5px solid var(--paper); }
  .envelope-flap .flap-url { position: absolute; left: 0; width: 100%; top: 57px; text-align: center; font-family: "Open Sans", sans-serif; font-size: 6px; letter-spacing: 0.8px; color: var(--paper); }
  .envelope-fold { position: absolute; left: 0; bottom: 0; width: 334px; height: 80px; background: linear-gradient(180deg, #fafafa, #ececec); clip-path: polygon(0 100%, 50% 0, 100% 100%); }

  .card .brand { left: 20px; top: 21px; }
  .card .brand-mark { width: 26px; height: 26px; margin-right: 9px; }
  .card .brand-name { font-size: 8.5px; }
</style>
</head>
<body>
<svg width="0" height="0" style="position:absolute" aria-hidden="true">
  <defs>
    <symbol id="icon-pin" viewBox="0 0 10 10"><path d="M5 0a3.4 3.4 0 0 0-3.4 3.4C1.6 6 5 10 5 10s3.4-4 3.4-6.6A3.4 3.4 0 0 0 5 0zm0 4.8a1.4 1.4 0 1 1 0-2.8 1.4 1.4 0 0 1 0 2.8z"/></symbol>
    <symbol id="icon-phone" viewBox="0 0 10 10"><path d="M2.2 0.5l1.6 2.1-1 1.1a6 6 0 0 0 3.5 3.5l1.1-1 2.1 1.6-0.9 1.7C4.5 9.2 0.8 5.5 0.5 1.4z"/></symbol>
    <symbol id="icon-fax" viewBox="0 0 10 10"><path d="M2.5 0.5h5v2.5h-5zM0.5 3.5h9v4h-2v2h-5v-2h-2zM3.5 6.5v2h3v-2z"/></symbol>
    <symbol id="icon-mail" viewBox="0 0 10 10"><path d="M0.5 2h9v6h-9zM1 2.5l4 3 4-3v-0.3h-8z"/></symbol>
    <symbol id="icon-web" viewBox="0 0 10 10"><path d="M5 0.5a4.5 4.5 0 1 0 0 9 4.5 4.5 0 0 0 0-9zm0 1.3c0.6 0.6 1 1.7 1.1 3H3.9C4 3.5 4.4 2.4 5 1.8zm-1.1 3.9h2.2c-0.1 1.3-0.5 2.4-1.1 3-0.6-0.6-1-1.7-1.1-3z"/></symbol>
  </defs>
</svg>

<main class="canvas">

  <section class="sheet letterhead" aria-label="Letterhead">
    <div class="ghost-square" aria-hidden="true"></div>
    <div class="brand">
      <div class="brand-mark" aria-hidden="true"></div>
      <div class="brand-name"><span>Meridian</span><span>Residential</span><span>Services, Inc.</span></div>
    </div>
    <p class="letter-body">Lorem ipsum dolor sit amet, consectetur adipiscing elit. Donec orci purus, luctus vitae dignissim eu, iaculis sed purus. Vivamus faucibus, ipsum nec aliquet viverra, leo mauris condimentum ligula, sit amet sagittis enim ligula quis arcu. Nam egestas tortor id nisi porttitor mattis. In tortor ante, ultricies in suscipit a, tempus non massa. Vivamus et auctor mi. Fusce vel massa nulla. Phasellus nec eros mauris, et scelerisque orci. Donec malesuada orci vitae nulla accumsan porta a id massa. Quisque accumsan iaculis magna sit amet fringilla. Maecenas consequat, magna eget tincidunt semper, odio nibh rutrum mi, id feugiat ante nisi eu risus. Vestibulum nunc orci, rhoncus a placerat in, ultricies in mi. Cras mattis varius eros, vel fringilla nisi suscipit eget.</p>
    <div class="signature" role="img" aria-label="Handwritten signature of the manager"></div>
    <p class="signer">Dana Ellison, Manager</p>
    <div class="contact-band">
      <div class="line-address"><svg><use href="#icon-pin"/></svg><b>MRS, Inc.</b> 4120 Harbor View Road, Juneau, Alaska 99801</div>
      <div class="line-reach"><svg><use href="#icon-phone"/></svg>555-210-4418 <svg><use href="#icon-fax"/></svg>555-210-4419 <svg><use href="#icon-mail"/></svg>hello@meridianres.com <svg><use href="#icon-web"/></svg>www.meridianres.com</div>
    </div>
  </section>

  <section class="sheet folder" aria-label="Presentation folder">
    <div class="brand">
      <div class="brand-mark" aria-hidden="true"></div>
      <div class="brand-name"><span>Meridian</span><span>Residential</span><span>Services, Inc.</span></div>
    </div>
    <div class="contact-band">
      <div class="line-address"><svg><use href="#icon-pin"/></svg><b>MRS, Inc.</b> 4120 Harbor View Road, Juneau, Alaska 99801</div>
      <div class="line-reach"><svg><use href="#icon-phone"/></svg>555-210-4418 <svg><use href="#icon-fax"/></svg>555-210-4419 <svg><use href="#icon-mail"/></svg>hello@meridianres.com <svg><use href="#icon-web"/></svg>www.meridianres.com</div>
    </div>
  </section>

  <section class="sheet envelope" aria-label="Envelope back">
    <div class="envelope-fold" aria-hidden="true"></div>
    <div class="envelope-flap">
      <div class="flap-mark" aria-hidden="true"></div>
      <p class="flap-url">www.meridianres.com</p>
    </div>
  </section>

  <section class="sheet card" aria-label="Envelope front">
    <div class="ghost-square" aria-hidden="true"></div>
    <div class="brand">
      <div class="brand-mark" aria-hidden="true"></div>
      <div class="brand-name"><span>Meridian</span><span>Residential</span><span>Services, Inc.</span></div>
    </div>
    <div class="contact-band">
      <div class="line-address"><svg><use href="#icon-pin"/></svg><b>MRS, Inc.</b> 4120 Harbor View Road, Juneau, Alaska 99801</div>
      <div class="line-reach"><svg><use href="#icon-phone"/></svg>555-210-4418 <svg><use href="#icon-fax"/></svg>555-210-4419 <svg><use href="#icon-mail"/></svg>hello@meridianres.com <svg><use href="#icon-web"/></svg>www.meridianres.com</div>
    </div>
  </section>

</main>
</body>
</html>
```